Telecommunications/Power civil contractor needs business card design

Were a new telecommunications/power underground civil contractor that is looking for a new business card design. Our company colours are silver or grey and orange. Feel free to use the white background logo or the black background logo.

Target Market(s)

Local contractors, utility companies, private sector mining/energy companies, developers.

Industry/Entity Type

Telecommunications

Contact Information for Business Card

Each card will need the following info:
Persons name:
Title:
E-mail:
Phone number:
Shop Address:
Mailing Address:

Requirements
Must have
• Each card will need the following info:
• Persons name:
• Title:
• E-mail:
• Phone number:
• Shop Address:
• Mailing Address:

```html
<!DOCTYPE html>
<html lang="en">
<head>
<meta charset="utf-8">
<title>Ridgeline Conduit Inc – Business Card</title>
<link rel="stylesheet" href="https://fonts.googleapis.com/css2?family=Arimo:wght@400;700&display=swap">
<style>
  :root {
    --backdrop: #4a403b;
    --card: #1c1c1d;
    --orange: #f2581f;
    --silver: #a9a9ab;
    --silver-light: #c9c9cb;
    --white: #f4f4f4;
    --rule: #8a8a8a;
  }
  * { margin: 0; padding: 0; box-sizing: border-box; }
  html, body {
    width: 1200px; height: 787px; overflow: hidden;
    background: var(--backdrop);
    font-family: "Arimo", Arial, sans-serif;
  }
  .stage {
    width: 1200px; height: 787px;
    display: flex; align-items: center; justify-content: center; gap: 40px;
  }
  .card {
    width: 540px; height: 309px;
    background: var(--card);
    position: relative;
    box-shadow: 0 10px 30px rgba(0,0,0,.45);
  }
  /* Front */
  .card--front {
    display: flex; flex-direction: column; align-items: center; justify-content: center; gap: 18px;
  }
  .brand-dot {
    width: 84px; height: 84px; border-radius: 50%;
    border: 8px solid var(--silver);
  }
  .brand-name {
    color: var(--orange); font-weight: 700; font-size: 30px; letter-spacing: 1px;
    text-transform: uppercase; text-align: center; line-height: 1.15;
    white-space: nowrap;
  }
  /* Back */
  .card--back { display: flex; align-items: center; }
  .back-brand {
    width: 250px; display: flex; flex-direction: column; align-items: center; gap: 14px;
  }
  .back-brand .brand-dot { width: 120px; height: 120px; border-width: 10px; }
  .back-brand .brand-name { font-size: 17px; letter-spacing: .5px; }
  .divider {
    width: 1px; height: 230px; flex: none;
    background: linear-gradient(to bottom, transparent, var(--rule), transparent);
  }
  .details { padding-left: 24px; color: var(--white); font-size: 15px; line-height: 1.3; }
  .person-name { color: var(--orange); font-weight: 700; font-size: 19px; }
  .person-title { color: var(--silver-light); margin-bottom: 7px; }
  .address { margin-bottom: 6px; }
  .address-label { color: var(--silver); font-weight: 700; font-size: 12px; text-transform: uppercase; letter-spacing: .5px; }
  .contact-list { list-style: none; margin-top: 2px; }
  .contact-list li { display: flex; align-items: center; gap: 10px; }
  .contact-list svg { width: 13px; height: 13px; fill: var(--orange); flex: none; }
</style>
</head>
<body>
<main class="stage">
  <section class="card card--front" aria-label="Card front">
    <div class="brand-dot"></div>
    <p class="brand-name">Ridgeline Conduit Inc</p>
  </section>

  <section class="card card--back" aria-label="Card back">
    <div class="back-brand">
      <div class="brand-dot"></div>
      <p class="brand-name">Ridgeline Conduit Inc</p>
    </div>
    <div class="divider"></div>
    <div class="details">
      <p class="person-name">Mark Halden</p>
      <p class="person-title">President</p>
      <p class="address"><span class="address-label">Shop</span><br>2170 Alder Creek Road, Millbrook, NY 12545</p>
      <p class="address"><span class="address-label">Mailing</span><br>PO Box 418, Millbrook, NY 12545</p>
      <ul class="contact-list">
        <li>
          <svg viewBox="0 0 16 16" aria-hidden="true"><path d="M3 1l3 3-2 2c1 2 3 4 5 5l2-2 3 3-2 3C7 15 1 9 0 3z"/></svg>
          555 0142 7781
        </li>
        <li>
          <svg viewBox="0 0 16 16" aria-hidden="true"><path d="M0 3h16v1L8 9 0 4zM0 6l8 5 8-5v7H0z"/></svg>
          mark@ridgeline.co
        </li>
        <li>
          <svg viewBox="0 0 16 16" aria-hidden="true"><circle cx="8" cy="8" r="8"/></svg>
          www.ridgeline.co
        </li>
      </ul>
    </div>
  </section>
</main>
</body>
</html>
```